Cobalt Ridge Electric Needs A Logo Design

We need a logo for my new company based out of Sacramento, Ca called Cobalt Ridge Electric. The name says it all, my electrical contracting business provides "Cobalt Ridge Professional Work" I'm open to any colors that pop and customers to say Wow. I would love to print my cards on metal.

Industry/Entity Type

Business

Contact Information for Business Card

The card needs to have as follows
Name of company: Cobalt Ridge Electric
My Name: Marco Delvane
Phone # 916-555-0173
CL# 2049381
Email: cobaltridgeelectric@mailnest.example
and a slogan that represent "COBALT RIDGE"

Requirements
Must have
• The card needs to have as follows
• Name of company: Cobalt Ridge Electric
• My Name : Marco Delvane
• Phone # 916-555-0173
• CL# 2049381
• Email: cobaltridgeelectric@mailnest.example
• and a slogan that represent "COBALT RIDGE"
Nice to have
• popping colors
• electrical Arcing

```html
<!DOCTYPE html>
<html lang="en">
<head>
<meta charset="utf-8">
<title>Cobalt Ridge Electric – Business Card</title>
<link rel="stylesheet" href="https://fonts.googleapis.com/css2?family=Montserrat:wght@400;700&family=Poppins:wght@300;400&display=swap">
<style>
  :root {
    --canvas: #e9e7e3;
    --card: #ffffff;
    --blue: #2f86c6;
    --grey-ring: #8a8a8a;
    --text-grey: #4a4a4a;
  }
  * { margin: 0; padding: 0; box-sizing: border-box; }
  html, body {
    width: 1200px; height: 1022px; overflow: hidden;
    background: var(--canvas);
  }
  .stage {
    width: 1200px; height: 1022px;
    display: flex; align-items: center; justify-content: center;
  }
  .card {
    position: relative;
    width: 910px; height: 520px;
    background: var(--card);
    box-shadow: 0 6px 24px rgba(0,0,0,0.12);
  }
  .brand {
    position: absolute;
    left: 40px; top: 150px;
    width: 380px;
    display: flex; flex-direction: column; align-items: center;
  }
  .brand-circle {
    width: 150px; height: 150px;
    border: 12px solid var(--grey-ring);
    border-radius: 50%;
  }
  .brand-name {
    margin-top: 26px;
    font-family: "Montserrat", sans-serif;
    font-weight: 400;
    font-size: 28px;
    letter-spacing: 0.4px;
    color: var(--blue);
    text-transform: uppercase;
    white-space: nowrap;
  }
  .divider {
    position: absolute;
    left: 440px; top: 150px;
    width: 2px; height: 220px;
    background: linear-gradient(to bottom, rgba(47,134,198,0), var(--blue) 25%, var(--blue) 75%, rgba(47,134,198,0));
  }
  .contact {
    position: absolute;
    left: 470px; top: 178px;
  }
  .person-name {
    font-family: "Montserrat", sans-serif;
    font-weight: 700;
    font-size: 30px;
    color: var(--blue);
    text-transform: uppercase;
    letter-spacing: 0.5px;
    margin-bottom: 18px;
  }
  .contact-line {
    display: flex; align-items: center; gap: 12px;
    font-family: "Poppins", sans-serif;
    font-weight: 300;
    font-size: 18px;
    color: var(--text-grey);
    line-height: 30px;
    white-space: nowrap;
  }
  .contact-line svg { width: 15px; height: 15px; flex: none; }
</style>
</head>
<body>
<main class="stage">
  <section class="card">
    <div class="brand">
      <div class="brand-circle"></div>
      <div class="brand-name">Cobalt Ridge Electric</div>
    </div>

    <div class="divider"></div>

    <div class="contact">
      <div class="person-name">Marco Delvane</div>
      <div class="contact-line">
        <svg viewBox="0 0 16 16" aria-hidden="true"><rect x="2" y="3" width="12" height="10" rx="1" fill="none" stroke="#2f86c6" stroke-width="1.6"/></svg>
        <span>2049381</span>
      </div>
      <div class="contact-line">
        <svg viewBox="0 0 16 16" aria-hidden="true"><path d="M4 2 L6.5 5 L5 6.5 Q6.5 9.5 9.5 11 L11 9.5 L14 12 L12 14 Q5 13 2 4 Z" fill="#2f86c6"/></svg>
        <span>916-555-0173</span>
      </div>
      <div class="contact-line">
        <svg viewBox="0 0 16 16" aria-hidden="true"><rect x="1.5" y="3.5" width="13" height="9" fill="none" stroke="#2f86c6" stroke-width="1.6"/><path d="M1.5 3.5 L8 9 L14.5 3.5" fill="none" stroke="#2f86c6" stroke-width="1.6"/></svg>
        <span>cobaltridgeelectric@mailnest.example</span>
      </div>
    </div>
  </section>
</main>
</body>
</html>
```